Commercial Loan Originator Business Card (CHANGE COLORS SCHEME)

CHANGE COLOR SCHEME - SAME DESIGN

Name Marlene Agate
Title Commercial Loan Originator
Office (800) 417-2906 x68
Direct (240) 615-2043
Email freshgreens4life@quillbox.example

Name Dale Morrow
Office (800) 417-2906 x70
Direct (410) 392-5184
Email d.morthehomeguy@quillbox.example

Name Leonard Vasko
Office (800) 417-2906 x71
Direct (215) 463-0712
Email l.vasko41@quillbox.example

Name Gwen Halsey
Office (800) 417-2906 x
Direct (202) 548-1370
Email ghalsey63@quillbox.example

Name Mirna Ashby
Office (800) 417-2906 x72
Direct (240) 871-4526
Email tristatehomelending@quillbox.example

```html
<!DOCTYPE html>
<html lang="en">
<head>
<meta charset="utf-8">
<title>Marlene Agate – Business Card</title>
<link rel="stylesheet" href="https://fonts.googleapis.com/css2?family=Poppins:wght@400;500;800&display=swap">
<style>
  :root {
    --backdrop: #d6d9d3;
    --base: #0d2b24;
    --base-glow: #1a4a3d;
    --accent: #e6ad2e;
    --white: #ffffff;
    --rule: #9fb8ae;
    --photo-light: #eceeea;
    --photo-tone: #c9b48a;
  }
  * { margin: 0; padding: 0; box-sizing: border-box; }
  html, body { width: 1200px; height: 1200px; overflow: hidden; }
  body {
    background: var(--backdrop);
    font-family: "Poppins", sans-serif;
    position: relative;
  }
  .card {
    position: absolute;
    left: 163px;
    width: 872px;
    height: 499px;
    background: var(--base);
    overflow: hidden;
    box-shadow: 0 10px 28px rgba(0, 0, 0, 0.35);
  }
  .card--front { top: 82px; }
  .card--back { top: 615px; }

  .accent-circle {
    position: absolute;
    border-radius: 50%;
    background: var(--accent);
  }
  .card--front .accent-circle { left: 77px; top: 415px; width: 300px; height: 300px; }
  .card--back .accent-circle { left: 80px; top: 347px; width: 306px; height: 306px; }

  .portrait-frame {
    position: absolute;
    left: 74px;
    top: -4px;
    width: 305px;
    height: 459px;
    border: 3px solid var(--white);
    border-top: none;
    border-radius: 0 0 152px 152px;
    overflow: hidden;
    box-shadow: 0 8px 12px rgba(0, 0, 0, 0.35);
  }
  .portrait {
    width: 100%;
    height: 100%;
    background: linear-gradient(180deg, var(--photo-light) 0%, var(--photo-light) 45%, #d9cbb0 68%, var(--photo-tone) 100%);
  }

  .name {
    position: absolute;
    font-weight: 800;
    line-height: 0.96;
    text-transform: uppercase;
    letter-spacing: 1px;
    white-space: nowrap;
  }
  .name__first { color: var(--accent); display: block; }
  .name__last { color: var(--white); display: block; }
  .card--front .name { left: 440px; top: 138px; font-size: 72px; }
  .card--back .name { left: 72px; top: 95px; font-size: 73px; }

  .rule {
    position: absolute;
    height: 1px;
    background: linear-gradient(90deg, transparent, var(--rule) 8%, var(--rule) 92%, transparent);
  }
  .card--front .rule { left: 434px; top: 305px; width: 368px; }
  .card--back .rule { left: 74px; top: 251px; width: 360px; }

  .title {
    position: absolute;
    color: var(--white);
    font-weight: 400;
    letter-spacing: 1px;
    white-space: nowrap;
  }
  .card--front .title { left: 455px; top: 341px; font-size: 21px; }
  .card--back .title { left: 72px; top: 270px; font-size: 23px; }

  .backdrop-portrait {
    position: absolute;
    right: 0;
    top: 0;
    width: 480px;
    height: 100%;
    background: radial-gradient(ellipse 60% 55% at 55% 40%, var(--base-glow) 0%, #14392f 50%, transparent 80%);
    opacity: 0.8;
  }

  .contacts {
    position: absolute;
    left: 434px;
    top: 351px;
    list-style: none;
  }
  .contact {
    display: flex;
    align-items: center;
    height: 28px;
    margin-bottom: 9px;
    color: var(--white);
    font-size: 19px;
    font-weight: 400;
    white-space: nowrap;
  }
  .contact__icon {
    width: 28px;
    height: 28px;
    border-radius: 50%;
    background: var(--accent);
    display: flex;
    align-items: center;
    justify-content: center;
    margin-right: 8px;
    flex: none;
  }
  .contact__icon svg { width: 15px; height: 15px; }
</style>
</head>
<body>

<section class="card card--front">
  <div class="accent-circle"></div>
  <div class="portrait-frame">
    <div class="portrait" role="img" aria-label="Portrait photo of Marlene Agate"></div>
  </div>
  <h1 class="name"><span class="name__first">Marlene</span><span class="name__last">Agate</span></h1>
  <div class="rule"></div>
  <p class="title">Commercial Loan Originator</p>
</section>

<section class="card card--back">
  <div class="backdrop-portrait" role="img" aria-label="Faint tinted portrait of Marlene Agate"></div>
  <div class="accent-circle"></div>
  <h2 class="name"><span class="name__first">Marlene</span><span class="name__last">Agate</span></h2>
  <div class="rule"></div>
  <p class="title">Commercial Loan Originator</p>

  <ul class="contacts">
    <li class="contact">
      <span class="contact__icon">
        <svg viewBox="0 0 16 16" fill="#fff"><path d="M1 5c0-2 3-3 7-3s7 1 7 3v1h-4V5H5v1H1z"/><path d="M4 7h8l2 7H2z"/><circle cx="8" cy="10.5" r="2" fill="#e6ad2e"/></svg>
      </span>
      (800) 417-2906 x68
    </li>
    <li class="contact">
      <span class="contact__icon">
        <svg viewBox="0 0 16 16" fill="#fff"><path d="M3.5 1.5l2.5 3-1.5 1.5c.8 2 2.5 3.7 4.5 4.5L10.5 9l3 2.5-1.5 2.5C7 14 2 9 1.5 3.5z"/></svg>
      </span>
      (240) 615-2043
    </li>
    <li class="contact">
      <span class="contact__icon">
        <svg viewBox="0 0 16 16" fill="none" stroke="#fff" stroke-width="1.6"><rect x="1.5" y="3.5" width="13" height="9"/><path d="M1.5 3.5l6.5 5 6.5-5"/></svg>
      </span>
      freshgreens4life@quillbox.example
    </li>
  </ul>
</section>

</body>
</html>
```